holloway paving service

Needs to have phone number 0418259730 and email markholloway@brightmail.com.au.
ABN 62318470915
name mark holloway

For all your concreting solutions
Excavation
Exposed & colour concrete
House & shed slabs
Driveways
Landing & steps

Contact Information for Business Card

ph 0418259730
email markholloway@brightmail.com.au.
ABN 62318470915
name mark holloway

```html
<!DOCTYPE html>
<html lang="en">
<head>
<meta charset="utf-8">
<title>Holloway Paving Service — Business Card</title>
<link rel="stylesheet" href="https://fonts.googleapis.com/css2?family=Lato:wght@400;700&family=Montserrat:wght@700&display=swap">
<style>
  :root {
    --bg: #1c1c1c;
    --card: #111111;
    --orange: #f26f21;
    --grey: #8a8a8a;
    --light: #d9d9d9;
    --white: #f2f2f2;
    --rule: #5a5a5a;
    --faint: #1b1b1b;
  }
  * { box-sizing: border-box; margin: 0; padding: 0; }
  html, body { width: 1200px; height: 900px; overflow: hidden; }
  body {
    background: var(--bg);
    font-family: "Lato", Arial, sans-serif;
    position: relative;
  }
  .card {
    position: absolute;
    left: 300px;
    width: 600px;
    height: 345px;
    background: var(--card);
    border-radius: 22px;
    overflow: hidden;
    box-shadow: 0 14px 34px rgba(0,0,0,0.55);
  }
  .card--back { top: 70px; }
  .card--front { top: 480px; }

  .faint-mark {
    position: absolute;
    width: 210px;
    height: 210px;
    background: var(--faint);
  }
  .card--back .faint-mark { left: 40px; top: 40px; transform: rotate(12deg); }
  .card--front .faint-mark { left: -70px; top: 20px; transform: rotate(12deg); }

  /* back side */
  .services {
    position: absolute;
    left: 205px;
    top: 125px;
    width: 370px;
  }
  .services__tagline {
    color: var(--orange);
    font-size: 16px;
    letter-spacing: 0.3px;
    margin-bottom: 14px;
    white-space: nowrap;
  }
  .services__row {
    color: var(--light);
    font-size: 14px;
    display: flex;
    align-items: center;
    gap: 10px;
    margin-bottom: 10px;
    white-space: nowrap;
  }
  .services__row--first { padding-left: 26px; }
  .bullet {
    width: 8px; height: 8px;
    background: var(--orange);
    transform: rotate(45deg);
    flex: none;
  }

  /* front side */
  .brand {
    position: absolute;
    left: 210px;
    top: 70px;
    display: flex;
    align-items: center;
    gap: 16px;
  }
  .brand__square {
    width: 56px; height: 56px;
    background: var(--orange);
    flex: none;
  }
  .brand__divider {
    width: 2px; height: 60px;
    background: var(--orange);
  }
  .brand__name {
    color: var(--orange);
    font-weight: 700;
    font-size: 19px;
    letter-spacing: 0.5px;
    text-transform: uppercase;
    white-space: nowrap;
  }
  .brand-rule {
    position: absolute;
    left: 300px; top: 150px;
    width: 270px; height: 1px;
    background: var(--rule);
  }
  .abn {
    position: absolute;
    right: 30px; top: 192px;
    color: var(--white);
    font-size: 15px;
  }
  .person {
    position: absolute;
    left: 40px; bottom: 34px;
    width: 530px;
  }
  .person__heading {
    display: flex;
    align-items: center;
    gap: 12px;
    margin-bottom: 12px;
  }
  .person__name {
    font-family: "Montserrat", Arial, sans-serif;
    font-weight: 700;
    font-size: 20px;
    text-transform: uppercase;
    white-space: nowrap;
  }
  .person__first { color: var(--orange); }
  .person__last { color: var(--grey); }
  .person__rule { flex: 1; height: 1px; background: var(--rule); }
  .contact {
    display: flex;
    align-items: center;
    gap: 10px;
    color: var(--white);
    font-size: 17px;
    margin-top: 6px;
  }
  .contact svg { width: 15px; height: 15px; flex: none; }
</style>
</head>
<body>

<section class="card card--back" aria-label="Business card back">
  <div class="faint-mark" aria-hidden="true"></div>
  <div class="services">
    <p class="services__tagline">FOR ALL YOUR CONCRETING SOLUTIONS</p>
    <p class="services__row services__row--first">Excavation <span class="bullet"></span> Exposed &amp; colour concrete</p>
    <p class="services__row">House &amp; shed slabs <span class="bullet"></span> Driveways <span class="bullet"></span> Landing &amp; steps</p>
  </div>
</section>

<section class="card card--front" aria-label="Business card front">
  <div class="faint-mark" aria-hidden="true"></div>
  <div class="brand">
    <span class="brand__square" aria-hidden="true"></span>
    <span class="brand__divider" aria-hidden="true"></span>
    <span class="brand__name">Holloway Paving Service</span>
  </div>
  <div class="brand-rule" aria-hidden="true"></div>
  <p class="abn">ABN 62318470915</p>
  <div class="person">
    <div class="person__heading">
      <h1 class="person__name"><span class="person__first">Mark</span> <span class="person__last">Holloway</span></h1>
      <span class="person__rule" aria-hidden="true"></span>
    </div>
    <p class="contact">
      <svg viewBox="0 0 16 16" aria-hidden="true"><path fill="#f26f21" d="M3.5 1.5l2.5 0 1.2 3-1.6 1.2a8 8 0 0 0 4.7 4.7l1.2-1.6 3 1.2v2.5c0 .8-.7 1.5-1.5 1.5A12.5 12.5 0 0 1 2 3c0-.8.7-1.5 1.5-1.5z"/></svg>
      0418259730
    </p>
    <p class="contact">
      <svg viewBox="0 0 16 16" aria-hidden="true"><rect x="1" y="3" width="14" height="10" fill="#f26f21"/><path d="M1 3.5l7 5 7-5" fill="none" stroke="#111" stroke-width="1.4"/></svg>
      markholloway@brightmail.com.au
    </p>
  </div>
</section>

</body>
</html>
```